High Tech Real Estate Startup needs a business card

We are developing an innovative real estate marketing product based around advanced search and virtual reality.

We talk to people, we need business cards.

Target Market(s)

The target market is technology professionals and realtors.

Contact Information for Business Card

The information to be included will include

Name
Title
Phone Number
E-mail Address
www.zelquin.com

It should use simple iconography for each one of those fields.

Font styles to use
Other font styles liked:
• Co, Jubilat, Avenir

Colors

Designer to choose colors to be used in the design.

Requirements
Must have
• Clean aesthetic,
• Good use of negative space.
• It should use our company logo, shown in the attached file. It is able to use the negative of that logo (coloured font and white background) and I have attached other acceptable accent colours in a swatch file.
Should not have
• Should not be too busy
• No extraneous text (slogans, tag lines etc)

```html
<!DOCTYPE html>
<html lang="en">
<head>
<meta charset="utf-8">
<title>Zelquin Business Card</title>
<link href="https://fonts.googleapis.com/css2?family=Open+Sans:wght@400;600&display=swap" rel="stylesheet">
<style>
  :root {
    --backdrop: #3a3a3c;
    --card: #1f1f21;
    --gloss: #0e0e0f;
    --teal: #3bb8bd;
    --ink: #e9e9ea;
  }
  * { margin: 0; padding: 0; box-sizing: border-box; }
  html, body { width: 799px; height: 1200px; overflow: hidden; }
  body {
    background: var(--backdrop);
    font-family: "Open Sans", Arial, sans-serif;
    display: flex;
    flex-direction: column;
    justify-content: space-around;
    align-items: center;
  }
  .card {
    position: relative;
    width: 620px;
    height: 360px;
    background: var(--card);
    border-radius: 28px;
  }
  .card-front .wordmark {
    position: absolute;
    top: 50%;
    left: 50%;
    transform: translate(-50%, -50%);
    font-size: 64px;
    font-weight: 600;
    letter-spacing: 4px;
    color: var(--gloss);
  }
  .card-back .wordmark {
    position: absolute;
    top: 60px;
    right: 44px;
    font-size: 56px;
    font-weight: 600;
    letter-spacing: 3px;
    color: var(--teal);
  }
  .identity {
    position: absolute;
    left: 44px;
    right: 44px;
    top: 226px;
    display: flex;
    align-items: baseline;
    gap: 16px;
    padding-bottom: 10px;
    border-bottom: 1px solid var(--teal);
  }
  .person-name { font-size: 22px; font-weight: 600; color: var(--ink); }
  .person-title { font-size: 15px; font-weight: 600; color: var(--teal); }
  .contacts {
    position: absolute;
    left: 44px;
    right: 44px;
    top: 284px;
    display: flex;
    gap: 26px;
    list-style: none;
  }
  .contact-item {
    display: flex;
    align-items: center;
    gap: 8px;
    font-size: 15px;
    color: var(--ink);
  }
  .contact-icon { width: 18px; height: 18px; flex: none; }
</style>
</head>
<body>
  <section class="card card-front">
    <div class="wordmark">ZELQUIN</div>
  </section>

  <section class="card card-back">
    <div class="wordmark">ZELQUIN</div>
    <div class="identity">
      <span class="person-name">Alex Dana Reed</span>
      <span class="person-title">Managing Director</span>
    </div>
    <ul class="contacts">
      <li class="contact-item">
        <svg class="contact-icon" viewBox="0 0 18 18" aria-hidden="true">
          <circle cx="9" cy="9" r="8.5" fill="none" stroke="#3bb8bd"/>
          <path d="M6 5.2l1.6-.3.8 2-1 .8a5 5 0 0 0 2.9 2.9l.8-1 2 .8-.3 1.6c-3.6.3-7.1-3.2-6.8-6.8z" fill="#3bb8bd"/>
        </svg>
        555.555.5555
      </li>
      <li class="contact-item">
        <svg class="contact-icon" viewBox="0 0 18 18" aria-hidden="true">
          <circle cx="9" cy="9" r="8.5" fill="none" stroke="#3bb8bd"/>
          <rect x="4.8" y="6" width="8.4" height="6" rx=".6" fill="#3bb8bd"/>
          <path d="M5 6.4l4 3 4-3" fill="none" stroke="#1f1f21" stroke-width=".9"/>
        </svg>
        alexreed@zelquin.com
      </li>
      <li class="contact-item">
        <svg class="contact-icon" viewBox="0 0 18 18" aria-hidden="true">
          <circle cx="9" cy="9" r="8.5" fill="none" stroke="#3bb8bd"/>
          <circle cx="9" cy="9" r="4.5" fill="none" stroke="#3bb8bd" stroke-width="1.1"/>
          <path d="M4.5 9h9M9 4.5c-2 2.5-2 6.5 0 9M9 4.5c2 2.5 2 6.5 0 9" fill="none" stroke="#3bb8bd" stroke-width=".9"/>
        </svg>
        www.zelquin.com
      </li>
    </ul>
  </section>
</body>
</html>
```